Landing Page Design for Adult Dating Age Verification (18+)

The objective of this task is to design a visually appealing pre-landing page for the adult dating site "Quillmera (site: https://quillmera.com/)" with an age verification mechanism. The pre-landing page will feature two buttons that redirect visitors to the main offer. The design should also include a footer block that includes links to the terms of use, privacy policy, and contact us pages.

Design Requirements:
Develop an age verification section prominently displayed on the pre-landing page.
Design the section to include two buttons labeled "Yes" and "No" for visitors to confirm their age.
Ensure the section is visually appealing and clearly communicates the purpose of age verification.

Visual Appeal:
Create a visually appealing design that aligns with the branding and theme of the "Quillmera" adult dating site.
Use suitable color schemes, typography, and graphics to enhance the overall visual appeal of the pre-landing page.

Layout and Navigation:
Design an engaging and intuitive layout that encourages visitors to interact with the page and proceed to the main offer.
Ensure clear and visible navigation elements that direct visitors to the main offer or provide additional information.

Responsive Design:
Develop a responsive design that provides a seamless user experience across various devices, including desktop and mobile.
Ensure the design elements and layout adapt well to different screen sizes and resolutions.

File Formats and Assets:
Deliver the final design in PSD, AI, or Sketch format, ensuring that the files are well-organized and layered.
Include any necessary images or assets used in the design, ensuring they are of high quality and optimized for web use.

```html
<!DOCTYPE html>
<html lang="en">
<head>
<meta charset="utf-8">
<title>Quillmera – Age Verification</title>
<link rel="stylesheet" href="https://fonts.googleapis.com/css2?family=EB+Garamond:wght@400&family=Open+Sans:wght@400;600&family=Playfair+Display:wght@700&display=swap">
<style>
  :root {
    --lilac: #c9a0cb;
    --lilac-light: #e6c7ef;
    --lilac-border: #e0bfe6;
    --white: #ffffff;
    --footer-bg: #000000;
    --footer-text: #e2e2e2;
    --modal-bg: rgba(8, 4, 6, 0.62);
    --photo-a: #3b3036;
    --photo-b: #5c4a4f;
    --photo-c: #2a2026;
    --photo-d: #6e5a5c;
  }
  * { margin: 0; padding: 0; box-sizing: border-box; }
  html, body { width: 1200px; height: 600px; overflow: hidden; }
  body { position: relative; font-family: "Open Sans", sans-serif; background: var(--photo-c); }

  .hero-photo {
    position: absolute; left: 0; top: 0; width: 1200px; height: 565px;
    background:
      radial-gradient(ellipse at 75% 30%, var(--photo-d) 0%, transparent 55%),
      radial-gradient(ellipse at 20% 70%, var(--photo-b) 0%, transparent 60%),
      linear-gradient(135deg, var(--photo-a) 0%, var(--photo-b) 45%, var(--photo-c) 100%);
  }

  .brand {
    position: absolute; left: 111px; top: 36px;
    display: flex; align-items: center; gap: 12px;
  }
  .brand-dot { width: 30px; height: 30px; border-radius: 50%; background: var(--lilac-light); }
  .brand-name {
    font-family: "Playfair Display", serif; font-weight: 700;
    font-size: 34px; color: var(--white); line-height: 1;
  }

  .age-gate {
    position: absolute; left: 267px; top: 146px; width: 667px; height: 309px;
    background: var(--modal-bg); border-radius: 20px;
    display: flex; flex-direction: column; align-items: center;
  }
  .age-gate-question {
    margin-top: 78px;
    font-family: "EB Garamond", serif; font-weight: 400;
    font-size: 38px; color: var(--lilac-light); line-height: 1.2;
  }
  .age-gate-actions { display: flex; gap: 19px; margin-top: 38px; }
  .age-button {
    width: 126px; height: 52px; border-radius: 26px;
    display: flex; align-items: center; justify-content: center;
    font-weight: 600; font-size: 19px; color: var(--white); text-decoration: none;
  }
  .age-button--yes { background: var(--lilac); }
  .age-button--no { border: 2px solid var(--lilac-border); background: transparent; }

  .site-footer {
    position: absolute; left: 0; bottom: 0; width: 1200px; height: 35px;
    background: var(--footer-bg); color: var(--footer-text);
    display: flex; align-items: center; justify-content: space-between;
    padding: 0 111px; font-size: 15px;
  }
  .footer-links { display: flex; align-items: center; gap: 14px; }
  .footer-links a { color: var(--footer-text); text-decoration: none; }
  .footer-sep { color: var(--footer-text); }
</style>
</head>
<body>
  <div class="hero-photo" role="img" aria-label="Romantic photograph of a couple embracing on a bed"></div>

  <a class="brand" href="https://quillmera.com/">
    <span class="brand-dot"></span>
    <span class="brand-name">Quillmera</span>
  </a>

  <section class="age-gate">
    <h1 class="age-gate-question">Are you over 18 years of age?</h1>
    <div class="age-gate-actions">
      <a class="age-button age-button--yes" href="https://quillmera.com/">Yes</a>
      <a class="age-button age-button--no" href="#">No</a>
    </div>
  </section>

  <footer class="site-footer">
    <span class="copyright">2023 Quillmera. All Rights Reserved.</span>
    <nav class="footer-links">
      <a href="#">Terms of use</a><span class="footer-sep">|</span>
      <a href="#">Privacy Policy</a><span class="footer-sep">|</span>
      <a href="#">Contact Us</a>
    </nav>
  </footer>
</body>
</html>
```